HOME PAGE AND AND SECONDARY DESIGN FOR INTERNAL PAGES

Construction company looking for an easy to navagate professional serious greyscale website with a good clean feel simple clean menu and responsive friendly design. Our main clientele is commercial properties business owners and investors of rental properties. This website is going to be static HTML5 and would need multiple sizing files for clean fast rendering. Clean and accurate design files a must so if your experienced awesome modern greyscale designer let's get started I need this done as soon as possible.

Industry/Entity Type

construction, electrical, plumbing, commercial build outs

Number of Pages Required

2 page

Font styles to use
Sans Serif

Colors

Designer to choose only greyscale colors for use in the design.

Requirements
Must have
• Main Menu... Home, Services, Projects, About our team

```html
<!DOCTYPE html>
<html lang="en">
<head>
<meta charset="utf-8">
<title>Ironridge Build Works</title>
<link rel="stylesheet" href="https://fonts.googleapis.com/css2?family=Poppins:wght@300;400;500;600;700;800&family=Lato:wght@400;700&display=swap">
<style>
  :root {
    --black: #000000;
    --ink: #111111;
    --text: #222222;
    --muted: #444444;
    --white: #ffffff;
    --pill: #8c8c8c;
    --band: #8a8a8a;
    --light: #efefef;
    --hero-dark: #2c2c2c;
    --hero-mid: #6d6d6d;
  }
  * { box-sizing: border-box; margin: 0; padding: 0; }
  html, body { width: 1200px; height: 2898px; overflow: hidden; background: var(--white); }
  body { position: relative; font-family: "Lato", sans-serif; color: var(--text); }
  .abs { position: absolute; }

  /* Hero */
  .hero { position: absolute; left: 0; top: 0; width: 1200px; height: 545px; overflow: hidden;
    background: linear-gradient(100deg, #1e1e1e 0%, #3a3a3a 20%, #5e5e5e 45%, #4a4a4a 70%, #2e2e2e 100%); }
  .hero-photo { position: absolute; inset: 0;
    background: radial-gradient(ellipse at 60% 45%, rgba(150,150,150,.35), transparent 60%),
                linear-gradient(180deg, rgba(0,0,0,.25), rgba(0,0,0,.05) 60%, rgba(0,0,0,.3)); }
  .brand { position: absolute; left: 107px; top: 60px; width: 170px; text-align: center;
    font-family: "Poppins", sans-serif; font-weight: 700; font-size: 17px; color: var(--white); letter-spacing: 1px; line-height: 1.1; }
  .brand small { display: block; font-weight: 400; font-size: 10px; letter-spacing: 3px; margin-top: 3px; }
  .nav { position: absolute; top: 32px; left: 0; width: 1200px; font-family: "Poppins", sans-serif; font-size: 17px; color: var(--white); }
  .nav a { position: absolute; color: var(--white); text-decoration: none; white-space: nowrap; }
  .nav .active-dot { position: absolute; left: 447px; top: 36px; width: 14px; height: 14px; border-radius: 50%; background: var(--white); }
  .btn-contact { position: absolute; left: 964px; top: 23px; width: 137px; height: 45px; border-radius: 23px; background: var(--black);
    color: var(--white); font-family: "Poppins", sans-serif; font-weight: 600; font-size: 17px; line-height: 45px; text-align: center; }
  .hero-title { position: absolute; top: 215px; width: 1200px; text-align: center; font-family: "Poppins", sans-serif; font-weight: 700;
    font-size: 51px; color: var(--white); letter-spacing: 1px; }
  .hero-sub { position: absolute; top: 291px; width: 1200px; text-align: center; font-size: 17.5px; color: var(--white); }
  .btn-outline { position: absolute; left: 511px; top: 339px; width: 179px; height: 44px; border: 2px solid var(--white); border-radius: 22px;
    color: var(--white); font-family: "Poppins", sans-serif; font-weight: 600; font-size: 16px; line-height: 40px; text-align: center; }
  .arrow { position: absolute; top: 248px; }
  .hero-wave { position: absolute; left: 0; top: 440px; }

  /* Section titles */
  .section-title { position: absolute; width: 1200px; text-align: center; font-family: "Poppins", sans-serif; font-weight: 400;
    font-size: 40px; color: var(--black); letter-spacing: 1px; }
  .section-title b { font-weight: 700; }

  /* Services */
  .service-img { position: absolute; top: 667px; width: 316px; height: 273px; border-radius: 14px; }
  .service-box { position: absolute; top: 875px; width: 274px; height: 205px; background: var(--white); text-align: center; }
  .service-box.raised { box-shadow: 0 4px 10px rgba(0,0,0,.18); }
  .service-box h3 { margin-top: 14px; font-family: "Poppins", sans-serif; font-weight: 600; font-size: 19px; color: var(--ink); }
  .service-box p { margin: 16px auto 0; width: 240px; font-family: "Poppins", sans-serif; font-size: 13.5px; line-height: 20px; color: var(--text); }
  .btn-pill { position: absolute; width: 151px; height: 45px; border-radius: 23px; background: var(--pill); color: var(--white);
    font-family: "Poppins", sans-serif; font-weight: 600; font-size: 15px; line-height: 45px; text-align: center; }

  /* Team */
  .team-photo { position: absolute; left: 0; top: 1255px; width: 1200px; height: 550px;
    background: linear-gradient(180deg, #ffffff 0%, rgba(255,255,255,0) 28%),
                radial-gradient(ellipse at 50% 70%, #8a8a8a 0%, #a9a9a9 45%, #cfcfcf 100%); }
  .team-text { position: absolute; top: 1247px; width: 1200px; text-align: center; font-size: 15.5px; line-height: 26px; color: var(--text); }

  /* Projects */
  .projects { position: absolute; left: 0; top: 1805px; width: 1200px; height: 732px;
    background: linear-gradient(180deg, #f2f2f2 0%, #e2e2e2 30%, #9a9a9a 70%, #5c5c5c 100%); }
  .project { position: absolute; width: 234px; height: 234px; border-radius: 50%; }

  /* Footer */
  .footer { position: absolute; left: 0; top: 2537px; width: 1200px; height: 361px; background: var(--black); color: var(--white); }
  .footer-brand { position: absolute; left: 100px; top: 155px; width: 220px; text-align: center; font-family: "Poppins", sans-serif;
    font-weight: 700; font-size: 21px; letter-spacing: 1px; line-height: 1.1; }
  .footer-brand small { display: block; font-weight: 400; font-size: 12px; letter-spacing: 3px; margin-top: 4px; }
  .footer h4 { position: absolute; font-family: "Poppins", sans-serif; font-weight: 600; font-size: 16px; }
  .footer a { position: absolute; color: var(--white); text-decoration: none; font-size: 16px; white-space: nowrap; }
  .footer .help a { font-size: 15px; }
  .footer .divider { position: absolute; top: 50px; width: 1px; height: 201px; background: var(--white); }
  .contact-line { position: absolute; left: 856px; font-size: 16px; line-height: 26px; }
  .contact-icon { position: absolute; left: 811px; }
  .footer .rule { position: absolute; left: 89px; top: 297px; width: 1000px; height: 1px; background: #777; }
  .copyright { position: absolute; top: 315px; width: 1200px; text-align: center; font-family: "Poppins", sans-serif; font-size: 15px; }
</style>
</head>
<body>

<header class="hero">
  <div class="hero-photo" role="img" aria-label="Modern commercial building exterior in greyscale"></div>
  <div class="brand">IRONRIDGE BUILD<small>WORKS LLC</small></div>
  <nav class="nav">
    <a style="left:429px">Home</a>
    <a style="left:537px">Services</a>
    <a style="left:666px">Projects</a>
    <a style="left:791px">About our team</a>
    <span class="active-dot"></span>
  </nav>
  <div class="btn-contact">Contact Us</div>
  <svg class="arrow" style="left:72px" width="26" height="40" viewBox="0 0 26 40"><path d="M22 3 L5 20 L22 37" fill="none" stroke="#fff" stroke-width="4"/></svg>
  <svg class="arrow" style="left:1112px" width="26" height="40" viewBox="0 0 26 40"><path d="M4 3 L21 20 L4 37" fill="none" stroke="#fff" stroke-width="4"/></svg>
  <h1 class="hero-title">IRONRIDGE BUILD WORKS</h1>
  <p class="hero-sub">Our main clientele is commercial property business owners and investors of rental properties.</p>
  <div class="btn-outline">GET STARTED</div>
  <svg class="hero-wave" width="1200" height="105" viewBox="0 0 1200 105">
    <path d="M0 42 Q 300 70 620 60 Q 950 50 1200 13 L1200 105 L0 105 Z" fill="#fff"/>
    <path d="M0 60 Q 320 80 640 72 Q 960 64 1200 25 L1200 42 Q 950 92 620 102 Q 300 110 0 98 Z" fill="var(--band)"/>
  </svg>
</header>

<h2 class="section-title" style="top:585px">OUR <b>SERVICES</b></h2>

<section class="services">
  <div class="service-img" style="left:99px;background:linear-gradient(135deg,#9c9c9c,#5a5a5a 55%,#c8c8c8)" role="img" aria-label="Hand pointing at an architectural building model"></div>
  <div class="service-img" style="left:442px;background:linear-gradient(180deg,#e6e6e6,#9a9a9a 55%,#4e4e4e)" role="img" aria-label="Engineers in hard hats at a construction site"></div>
  <div class="service-img" style="left:784px;background:linear-gradient(180deg,#5a5a5a,#d8d8d8 40%,#a0a0a0)" role="img" aria-label="Empty commercial interior ready for build out"></div>

  <div class="service-box" style="left:120px">
    <h3>LOREM IPSUM DOLOR</h3>
    <p>Sed ut perspiciatis unde omnis issitvoluptatemaccusantium doloremque laudantium, totam rem aperiam, eaque ipsa&nbsp; Sed ut perspiciatis unde omnis</p>
  </div>
  <div class="service-box raised" style="left:463px">
    <h3>LOREM IPSUM DOLOR</h3>
    <p>Sed ut perspiciatis unde omnis issitvoluptatemaccusantium doloremque laudantium, totam rem aperiam, eaque ipsa&nbsp; Sed ut perspiciatis unde omnis</p>
  </div>
  <div class="service-box" style="left:805px">
    <h3>LOREM IPSUM DOLOR</h3>
    <p>Sed ut perspiciatis unde omnis issitvoluptatemaccusantium doloremque laudantium, totam rem aperiam, eaque ipsa&nbsp; Sed ut perspiciatis unde omnis</p>
  </div>

  <div class="btn-pill" style="left:182px;top:1054px">LEARN MORE</div>
  <div class="btn-pill" style="left:525px;top:1053px">LEARN MORE</div>
  <div class="btn-pill" style="left:867px;top:1054px">LEARN MORE</div>
</section>

<section class="team">
  <div class="team-photo" role="img" aria-label="Team of colleagues giving a celebratory high five in an office"></div>
  <h2 class="section-title" style="top:1178px;font-size:41px">ABOUT <b>OUR TEAM</b></h2>
  <p class="team-text">Lorem ipsum dolor sit amet, consectetur adipiscing elit, sed do eiusmod tempor incididunt ut labore et dolore magna aliqua.<br>Ut enim ad minim veniam, quis nostrud exercitation ullamco laboris nisi ut aliquip ex ea commodo consequat. Duis aute irure<br>dolor in reprehenderit in voluptate velit esse cillum dolore eu fugiat nulla pariatur.</p>
  <div class="btn-pill" style="left:525px;top:1352px">LEARN MORE</div>
</section>

<section class="projects" role="img" aria-label="Curved glass and steel roof structure in greyscale">
</section>
<h2 class="section-title" style="top:1848px">OUR <b>PROJECTS</b></h2>
<div class="project" style="left:100px;top:1949px;background:linear-gradient(160deg,#eaeaea,#9a9a9a 60%,#cfcfcf)" role="img" aria-label="Office building facade"></div>
<div class="project" style="left:360px;top:1949px;background:radial-gradient(circle at 60% 30%,#ffffff,#a8a8a8 45%,#4a4a4a)" role="img" aria-label="Looking up at a curved glass tower"></div>
<div class="project" style="left:612px;top:1949px;background:radial-gradient(circle at 50% 50%,#3a3a3a,#0e0e0e)" role="img" aria-label="Dark office interior with people in silhouette"></div>
<div class="project" style="left:872px;top:1949px;background:linear-gradient(180deg,#d8d8d8,#7a7a7a 55%,#b8b8b8)" role="img" aria-label="Modern waterfront residential building"></div>
<div class="project" style="left:227px;top:2203px;background:linear-gradient(135deg,#6a6a6a,#d0d0d0 60%,#9a9a9a)" role="img" aria-label="Handshake over a small house model"></div>
<div class="project" style="left:487px;top:2203px;background:linear-gradient(180deg,#f0f0f0,#c0c0c0 60%,#7a7a7a)" role="img" aria-label="Couple viewing an apartment with an agent"></div>
<div class="project" style="left:739px;top:2203px;background:linear-gradient(180deg,#bdbdbd,#8a8a8a 50%,#4f4f4f)" role="img" aria-label="Apartment blocks under a cloudy sky"></div>

<footer class="footer">
  <div class="footer-brand">IRONRIDGE BUILD<small>WORKS LLC</small></div>

  <h4 style="left:400px;top:50px">QUICK LINKS</h4>
  <a style="left:401px;top:116px">Home</a>
  <a style="left:401px;top:142px">Services</a>
  <a style="left:401px;top:168px">Projects</a>
  <a style="left:401px;top:194px">About our team</a>
  <span class="divider" style="left:543px"></span>

  <div class="help">
    <h4 style="left:601px;top:50px">HELP LINK</h4>
    <a style="left:602px;top:116px">Terms &amp; Conditions</a>
    <a style="left:602px;top:150px">Privacy Policy</a>
    <a style="left:602px;top:184px">About Us</a>
    <a style="left:602px;top:218px">Support</a>
  </div>
  <span class="divider" style="left:768px"></span>

  <h4 style="left:814px;top:48px">OUR LOCATION</h4>
  <svg class="contact-icon" style="top:127px" width="32" height="32" viewBox="0 0 32 32"><circle cx="16" cy="16" r="14.5" fill="none" stroke="#fff" stroke-width="1.5"/><path d="M16 24 C12 19 11 16.5 11 14.5 a5 5 0 0 1 10 0 C21 16.5 20 19 16 24 Z" fill="none" stroke="#fff" stroke-width="1.6"/><circle cx="16" cy="14.5" r="1.8" fill="#fff"/></svg>
  <div class="contact-line" style="top:112px">1420 Granite Ridge Road Ste 200<br>Millbrook texas 75010</div>
  <svg class="contact-icon" style="top:183px" width="32" height="32" viewBox="0 0 32 32"><circle cx="16" cy="16" r="14.5" fill="none" stroke="#fff" stroke-width="1.5"/><path d="M11 9.5 l3 0 l1.5 4 l-2 1.5 a9 9 0 0 0 4 4 l1.5 -2 l4 1.5 l0 3 a2 2 0 0 1 -2 2 A13 13 0 0 1 9 11.5 a2 2 0 0 1 2 -2 Z" fill="none" stroke="#fff" stroke-width="1.5" stroke-linejoin="round"/></svg>
  <div class="contact-line" style="top:186px">+1 555-014-2270</div>
  <svg class="contact-icon" style="top:241px" width="32" height="32" viewBox="0 0 32 32"><circle cx="16" cy="16" r="14.5" fill="none" stroke="#fff" stroke-width="1.5"/><rect x="9" y="11" width="14" height="10" rx="1.5" fill="none" stroke="#fff" stroke-width="1.5"/><path d="M9.5 12 L16 17 L22.5 12" fill="none" stroke="#fff" stroke-width="1.5"/></svg>
  <div class="contact-line" style="top:244px">hello@ironridgebuild.example</div>

  <span class="rule"></span>
  <p class="copyright">© copyrights 2023 <span style="font-size:17px">Ironridge Build Works</span> |&nbsp; All Rights Reserved</p>
</footer>

</body>
</html>
```